Tradeshwo display 8x10 high resolution backdrop

I created a backdrop I wanted to use via Chat GPT but the image isn't high quality enough for print so I want someone to recreate it as close as possible to my creation. See attached, TY!

```html
<!DOCTYPE html>
<html lang="en">
<head>
<meta charset="UTF-8">
<title>Quarvo Water Systems – Trade Show Backdrop</title>
<link href="https://fonts.googleapis.com/css2?family=Archivo:wght@400;500;600;700;800;900&family=Roboto+Condensed:wght@400;500;700&family=Montserrat:wght@500;700;800&display=swap" rel="stylesheet">
<style>
  :root {
    --navy: #0b1a3d;
    --navy-deep: #071330;
    --blue: #1f5fb8;
    --blue-bright: #2f86d6;
    --blue-dark: #173f8f;
    --ink: #111111;
    --white: #ffffff;
    --rule: #c9ced8;
  }
  * { margin: 0; padding: 0; box-sizing: border-box; }
  html, body { width: 1200px; height: 960px; overflow: hidden; background: var(--white); }
  .backdrop { position: relative; width: 1200px; height: 960px; overflow: hidden; background: var(--white); font-family: "Archivo", sans-serif; color: var(--ink); }

  /* Brand */
  .brand { position: absolute; left: 44px; top: 70px; display: flex; align-items: center; gap: 14px; }
  .brand-dot { width: 26px; height: 26px; border-radius: 50%; background: var(--blue-dark); }
  .brand-name { font-family: "Montserrat", sans-serif; font-weight: 800; color: var(--blue-dark); font-size: 76px; line-height: 1; letter-spacing: -1px; }
  .brand-full { position: absolute; left: 72px; top: 150px; font-family: "Montserrat", sans-serif; font-weight: 800; color: var(--blue-dark); font-size: 12.5px; }

  /* Value icons */
  .values { position: absolute; left: 352px; top: 74px; display: flex; list-style: none; }
  .value { display: flex; flex-direction: column; align-items: center; padding: 0 14px; border-right: 1px solid var(--rule); }
  .value:last-child { border-right: none; }
  .value svg { width: 46px; height: 46px; margin-bottom: 8px; }
  .value span { font-family: "Montserrat", sans-serif; font-weight: 500; font-size: 12.5px; line-height: 1.25; text-align: center; color: var(--ink); letter-spacing: .2px; }

  /* Hero photo */
  .hero-photo { position: absolute; right: 0; top: 0; width: 470px; height: 380px; }

  /* Headline */
  .headline { position: absolute; left: 45px; top: 224px; white-space: nowrap; }
  .headline-top { font-weight: 900; font-size: 45px; line-height: 1; letter-spacing: .3px; color: var(--ink); }
  .headline-main { font-weight: 900; font-size: 63px; line-height: 1; margin-top: 8px; word-spacing: 6px;
    background: linear-gradient(180deg, var(--blue-bright), var(--blue-dark)); -webkit-background-clip: text; background-clip: text; color: transparent; }
  .pillars { position: absolute; left: 44px; top: 348px; width: 736px; display: flex; align-items: center; gap: 16px; }
  .pillars .line { flex: 1; height: 2px; background: var(--blue); }
  .pillars p { font-weight: 800; font-size: 18px; letter-spacing: 3.6px; color: var(--ink); white-space: nowrap; }
  .pillars b { color: var(--blue-bright); font-size: 13px; margin: 0 3px; }

  /* Banner */
  .banner { position: absolute; left: 0; top: 394px; width: 792px; height: 41px; }
  .banner svg { position: absolute; inset: 0; }
  .banner p { position: absolute; left: 61px; top: 0; line-height: 41px; color: var(--white); font-weight: 800; font-size: 18.5px; letter-spacing: .3px; white-space: nowrap; }

  /* Feature tiles */
  .features { position: absolute; left: 876px; top: 376px; width: 324px; }
  .feature { position: relative; height: 78px; margin-bottom: 2px; display: flex; align-items: center; }
  .feature.tall { height: 93px; }
  .feature > svg.tile { position: absolute; inset: 0; width: 100%; height: 100%; }
  .feature .icon { position: relative; width: 46px; height: 46px; margin-left: 30px; flex: none; }
  .feature p { position: relative; margin-left: 16px; color: var(--white); font-weight: 800; font-size: 16.5px; line-height: 1.25; letter-spacing: .4px; }

  /* Products */
  .products { position: absolute; left: 38px; top: 484px; width: 822px; display: flex; }
  .product { width: 137px; display: flex; flex-direction: column; align-items: center; text-align: center; border-right: 1px solid #e2e5ea; padding: 0 3px; height: 240px; }
  .product:last-child { border-right: none; }
  .product-img { width: 104px; height: 108px; border-radius: 6px; }
  .product h3 { font-family: "Roboto Condensed", sans-serif; font-weight: 700; color: var(--blue-dark); font-size: 15px; line-height: 1.15; margin-top: 22px; white-space: nowrap; }
  .product h3.small { font-size: 14px; }
  .product p { font-family: "Roboto Condensed", sans-serif; font-weight: 400; font-size: 14.2px; line-height: 1.18; color: var(--ink); margin-top: 7px; }
  .product p strong { font-weight: 700; }

  /* Footer */
  .footer-wave { position: absolute; left: 0; top: 705px; width: 1200px; height: 255px; }
  .footer { position: absolute; left: 0; top: 840px; width: 1200px; height: 80px; color: var(--white); }
  .service { position: absolute; left: 74px; top: 6px; display: flex; gap: 16px; }
  .pin { width: 46px; height: 46px; margin-top: 6px; }
  .service p { font-weight: 500; font-size: 17px; line-height: 1.27; letter-spacing: .4px; }
  .service p strong { font-weight: 800; }
  .divider { position: absolute; top: 28px; width: 2px; height: 34px; background: var(--white); }
  .url { position: absolute; left: 456px; top: 32px; font-weight: 800; font-size: 28.5px; letter-spacing: .5px; white-space: nowrap; }
  .slogan { position: absolute; left: 872px; top: 24px; width: 260px; text-align: center; font-size: 17px; line-height: 1.25; letter-spacing: .4px; font-weight: 500; }
  .slogan strong { font-weight: 800; }
</style>
</head>
<body>
<main class="backdrop">

  <div class="brand">
    <span class="brand-dot"></span>
    <span class="brand-name">QWS</span>
  </div>
  <div class="brand-full">Quarvo Water Systems</div>

  <ul class="values">
    <li class="value">
      <svg viewBox="0 0 48 48" fill="none" stroke="#1f5fb8" stroke-width="2"><circle cx="24" cy="19" r="14"/><circle cx="24" cy="19" r="10"/><path d="M24 12l2.2 4.5 5 .7-3.6 3.5.9 5-4.5-2.4-4.5 2.4.9-5-3.6-3.5 5-.7z"/><path d="M15 30l-4 12 6-2 3 5 4-11M33 30l4 12-6-2-3 5-4-11"/></svg>
      <span>QUALITY<br>BRANDS</span>
    </li>
    <li class="value">
      <svg viewBox="0 0 48 48" fill="none" stroke="#1f5fb8" stroke-width="2"><path d="M24 3l3 5 5-2 1 5 5 1-2 5 5 3-5 3 2 5-5 1-1 5-5-2-3 5-3-5-5 2-1-5-5-1 2-5-5-3 5-3-2-5 5-1 1-5 5 2z"/><circle cx="24" cy="24" r="10"/><path d="M19 24l4 4 7-8"/></svg>
      <span>ENGINEERED<br>SOLUTIONS</span>
    </li>
    <li class="value">
      <svg viewBox="0 0 48 48" fill="none" stroke="#1f5fb8" stroke-width="2"><path d="M10 26v-4a14 14 0 0128 0v4"/><rect x="7" y="24" width="7" height="12" rx="2"/><rect x="34" y="24" width="7" height="12" rx="2"/><path d="M37 36c0 5-6 7-11 7"/><circle cx="24" cy="43" r="2"/></svg>
      <span>EXPERT<br>SUPPORT</span>
    </li>
    <li class="value">
      <svg viewBox="0 0 48 48" fill="none" stroke="#1f5fb8" stroke-width="2"><path d="M2 14l6-4 6 14-6 4zM46 14l-6-4-6 14 6 4z"/><path d="M13 14c4-2 8-3 11-1l-6 6c2 2 5 2 7 0l6-5 6 10M14 24l10 9c1.5 1.2 3.5-.5 2-2M19 26l8 7c1.5 1 3.2-.8 2-2M23 25l7 6c1.4 1 3.2-.8 2-2"/></svg>
      <span>TURNKEY<br>DELIVERY</span>
    </li>
  </ul>

  <svg class="hero-photo" viewBox="0 0 470 380" role="img" aria-label="Photo of a wastewater treatment plant with clarifier tanks reflecting a sunset sky">
    <defs>
      <linearGradient id="skyGrad" x1="0" y1="0" x2="0" y2="1">
        <stop offset="0" stop-color="#2f5f9e"/>
        <stop offset=".28" stop-color="#9fb7cf"/>
        <stop offset=".38" stop-color="#f2c06a"/>
        <stop offset=".46" stop-color="#35506a"/>
        <stop offset=".7" stop-color="#2b5a94"/>
        <stop offset="1" stop-color="#0c2556"/>
      </linearGradient>
    </defs>
    <path d="M0 0H470V380C380 375 300 350 240 300C160 235 80 120 0 0Z" fill="url(#skyGrad)"/>
    <path d="M0 0C80 120 160 235 240 300C300 350 380 375 470 380" fill="none" stroke="#1f5fb8" stroke-width="3"/>
  </svg>

  <div class="headline">
    <div class="headline-top">SOLUTIONS THAT</div>
    <div class="headline-main">KEEP WATER MOVING</div>
  </div>

  <div class="pillars">
    <span class="line"></span>
    <p>EXPERTISE<b>•</b>RELIABILITY<b>•</b>RESULTS</p>
    <span class="line"></span>
  </div>

  <div class="banner">
    <svg width="792" height="41" viewBox="0 0 792 41">
      <defs><linearGradient id="bannerGrad" x1="0" x2="1"><stop offset="0" stop-color="#1a56ad"/><stop offset=".6" stop-color="#2a78cc"/><stop offset="1" stop-color="#1f5fb8"/></linearGradient></defs>
      <path d="M0 0H770L792 20.5 770 41H0Z" fill="url(#bannerGrad)"/>
    </svg>
    <p>COMPLETE SOLUTIONS FOR THE WATER &amp; WASTEWATER INDUSTRY</p>
  </div>

  <section class="features">
    <div class="feature">
      <svg class="tile" viewBox="0 0 324 78" preserveAspectRatio="none"><path d="M22 0H324V78H22L0 39Z" fill="#0b1a3d"/></svg>
      <svg class="icon" viewBox="0 0 48 48" fill="none" stroke="#fff" stroke-width="1.8"><circle cx="24" cy="24" r="21"/><path d="M22 13c-5 7-8 11-8 15a8 8 0 0016 0c0-4-3-8-8-15z"/><path d="M29 14c-2.5 3.5-4 5.5-4 7.5a4 4 0 008 0c0-2-1.5-4-4-7.5z"/></svg>
      <p>WATER &amp;<br>WASTEWATER<br>EXPERTISE</p>
    </div>
    <div class="feature">
      <svg class="tile" viewBox="0 0 324 78" preserveAspectRatio="none"><path d="M22 0H324V78H22L0 39Z" fill="#0b1a3d"/></svg>
      <svg class="icon" viewBox="0 0 48 48" fill="none" stroke="#fff" stroke-width="2.4"><path d="M24 4l17 6v12c0 11-7 18-17 22C14 40 7 33 7 22V10z"/><path d="M16 24l6 6 11-12"/></svg>
      <p>TRUSTED<br>PRODUCTS</p>
    </div>
    <div class="feature">
      <svg class="tile" viewBox="0 0 324 78" preserveAspectRatio="none"><path d="M22 0H324V78H22L0 39Z" fill="#0b1a3d"/></svg>
      <svg class="icon" viewBox="0 0 48 48" fill="none" stroke="#fff" stroke-width="1.8"><path d="M10 26v-4a14 14 0 0128 0v4"/><rect x="7" y="24" width="7" height="12" rx="2"/><rect x="34" y="24" width="7" height="12" rx="2"/><path d="M37 36c0 5-6 7-11 7"/><circle cx="24" cy="43" r="2"/></svg>
      <p>LOCAL SUPPORT<br>YOU CAN COUNT ON</p>
    </div>
    <div class="feature tall">
      <svg class="tile" viewBox="0 0 324 93" preserveAspectRatio="none"><path d="M22 0H324V93H22L0 46.5Z" fill="#0b1a3d"/></svg>
      <svg class="icon" viewBox="0 0 48 48" fill="#fff"><rect x="3" y="36" width="6" height="8"/><rect x="12" y="30" width="6" height="14"/><rect x="21" y="26" width="6" height="18"/><rect x="30" y="20" width="6" height="24"/><rect x="39" y="14" width="6" height="30"/><path d="M4 30L30 10" stroke="#fff" stroke-width="2.4"/><path d="M26 6h12v10z"/><rect x="0" y="45" width="48" height="2"/></svg>
      <p>BUILT FOR<br>PERFORMANCE.<br>FOCUSED ON<br>YOUR SUCCESS.</p>
    </div>
  </section>

  <section class="products">
    <article class="product">
      <div class="product-img" role="img" aria-label="Blue split-case centrifugal pump" style="background:radial-gradient(circle,#3b6fd0,#1e48a0 60%,#fff 72%)"></div>
      <h3>PUMPS</h3>
      <p>Industry leading pumps built for performance, efficiency &amp; reliability.</p>
    </article>
    <article class="product">
      <div class="product-img" role="img" aria-label="Blue high efficiency electric motor" style="background:radial-gradient(circle,#3a70d2,#1c46a0 60%,#fff 72%)"></div>
      <h3>MOTORS</h3>
      <p>High efficiency<br>motors engineered<br>for durability and<br>long life.</p>
    </article>
    <article class="product">
      <div class="product-img" role="img" aria-label="Silver positive displacement blower" style="background:radial-gradient(circle,#c9cdd2,#8a9098 60%,#fff 72%)"></div>
      <h3>BLOWERS</h3>
      <p>Zephra PD positive displacement blowers for reliable, energy efficient performance.</p>
    </article>
    <article class="product">
      <div class="product-img" role="img" aria-label="Variable frequency drive cabinet with keypad" style="background:linear-gradient(90deg,#2c2f36,#3b4150 55%,#1f3d7a)"></div>
      <h3>VFD &amp; CONTROLS</h3>
      <p>Precision control and energy savings through advanced VFD solutions.</p>
    </article>
    <article class="product">
      <div class="product-img" role="img" aria-label="Blue control valve with actuator" style="background:radial-gradient(circle,#3a6cc9,#1d449c 55%,#fff 72%)"></div>
      <h3>AUTOMATION &amp;<br>VALVES</h3>
      <p>Smart automation and reliable valves for optimized system performance.</p>
    </article>
    <article class="product">
      <div class="product-img" role="img" aria-label="Illustration of a hand holding a gear with a water drop" style="background:radial-gradient(circle,#2f66c4,#1f4ea6 55%,#fff 72%)"></div>
      <h3 class="small">TURNKEY SOLUTIONS</h3>
      <p>Complete systems designed, integrated and supported by <strong>QWS.</strong></p>
    </article>
  </section>

  <svg class="footer-wave" viewBox="0 0 1200 255" preserveAspectRatio="none">
    <defs>
      <linearGradient id="waveGrad" x1="0" y1="0" x2="0" y2="1"><stop offset="0" stop-color="#13306e"/><stop offset=".35" stop-color="#0b1a3d"/><stop offset="1" stop-color="#071330"/></linearGradient>
      <linearGradient id="streak" x1="0" x2="1"><stop offset="0" stop-color="#1f5fb8"/><stop offset=".6" stop-color="#3d8fe6"/><stop offset="1" stop-color="#1a4fa8"/></linearGradient>
    </defs>
    <path d="M0 60C300 95 700 95 1200 0V255H0Z" fill="url(#waveGrad)"/>
    <path d="M0 60C300 95 700 95 1200 0V20C700 110 300 110 0 75Z" fill="url(#streak)"/>
    <path d="M0 95C400 125 800 110 1200 40" fill="none" stroke="#2f7fd6" stroke-width="2" opacity=".6"/>
  </svg>

  <footer class="footer">
    <div class="service">
      <svg class="pin" viewBox="0 0 46 46"><circle cx="23" cy="23" r="22" fill="#1f5fb8" stroke="#fff" stroke-width="1.5"/><path d="M23 10a8 8 0 00-8 8c0 6 8 16 8 16s8-10 8-16a8 8 0 00-8-8z" fill="#fff"/><circle cx="23" cy="18" r="3" fill="#1f5fb8"/></svg>
      <p><strong>SERVICING</strong><br>VIRGINIA | NORTH CAROLINA<br>MARYLAND | DELAWARE</p>
    </div>
    <span class="divider" style="left:424px"></span>
    <div class="url">www.qws-flowline.com</div>
    <span class="divider" style="left:850px"></span>
    <p class="slogan">YOUR PARTNER FOR<br><strong>A BETTER FLOW FORWARD</strong></p>
  </footer>

</main>
</body>
</html>
```